Collectibles expert needs a new business card design.

My current business card makes me look to high end. It may even make me look arrogant or too stuffy. I do work with high end clients and their items but most of my business is with average people with average items. My business name is Walter Brennick's Old Orchard Salvage Co. The idea was that I mine the streets helping people discover the treasures buried in their homes. That could be art, jewelry, coins, etc. The name and an older logo I used does not make immediate sense to most people. I tried to go with just my picture and name and that is the current card I am changing. I help people who need to downsize. Whether they are getting rid of one item, a collection or a house full of items I help them discover what they have, what it is worth and what are the best ways we can get the most for them. This may be a combination of estate sale (which I dont do) auction or sell directly to a dealer or collector. Usually it is a combination of these. My main goal is to help make sure they dont accidently sell a Picasso painting in a garage sale. I am uploading a copy of my old card and the old logo I used to use but the winning card design will need to be much different than these. You can learn a little more about me at www.walterjbrennick.example, www.oldorchardsalv.example and www.facebook.com/oosalco. I hope someone can look at what I do and come up with a very unique design that will be equally effective if my client is high income or if my client is low to mid income. I do not care if it is a one or two sided card as long as it conveys my contact information and a good representation of what I do.

Target Market(s)

People who are getting rid of items. These can be elderly couples or individuals that are moving to an active living community and will have less space so they need to sell items. This can also include the children of elder parents that dont want their stuff and want to find solutions to help them get rid of their items.

Contact Information for Business Card

The card should have my business name Walter Brennick's Old Orchard Salvage Co., phone number 555-302-71938, email walter@oldorchardsalvage.example and website www.oldorchardsalvage.example. Would also like to include Buyer, Broker, Consultant and Appraiser. We can put Walter J. Brennick, ISA on the opposite side of the company name since it includes my name as well.

Font styles to use
Sans Serif

Colors

Designer to choose colors to be used in the design.

Requirements
Must have
• My project must have a professional look. It must not alienate low income clients and should still be appealing to high value clients.

```html
<!DOCTYPE html>
<html lang="en">
<head>
<meta charset="utf-8">
<title>Old Orchard Salvage Co. — Business Card</title>
<link rel="stylesheet" href="https://fonts.googleapis.com/css2?family=Bebas+Neue&family=Lato:wght@400&display=swap">
<style>
  :root {
    --backdrop: #2a2a2a;
    --card: #ffffff;
    --ink: #2b2622;
    --slate: #58575a;
    --bronze: #9c7230;
    --copper: #c9712e;
  }
  * { margin: 0; padding: 0; box-sizing: border-box; }
  html, body { width: 1200px; height: 1200px; overflow: hidden; }
  body { background: var(--backdrop); position: relative; font-family: "Lato", sans-serif; }

  .card {
    position: absolute;
    top: 310px;
    width: 364px;
    height: 594px;
    background: var(--card);
    box-shadow: 0 3px 8px rgba(0,0,0,.45);
  }
  .card--front { left: 234px; }
  .card--back  { left: 627px; width: 369px; }

  .brand-mark {
    position: absolute;
    left: 0; right: 0;
    display: flex; flex-direction: column; align-items: center; gap: 14px;
  }
  .brand-mark__dot {
    width: 62px; height: 62px; border-radius: 50%;
    background: var(--bronze);
  }
  .brand-mark__name {
    font-family: "Bebas Neue", sans-serif;
    color: var(--slate);
    font-size: 40px;
    line-height: 1;
    text-align: center;
    letter-spacing: .5px;
  }
  .card--front .brand-mark { top: 120px; }

  .person {
    position: absolute; top: 382px; left: 0; right: 0; text-align: center;
  }
  .person__name {
    font-family: "Bebas Neue", sans-serif;
    font-size: 27px; color: var(--ink); letter-spacing: .3px; line-height: 1;
  }
  .person__role {
    margin-top: 6px; font-size: 16.5px; color: var(--bronze);
  }

  .contact-divider {
    position: absolute; top: 448px; left: 87px; width: 190px; height: 24px;
    display: flex; align-items: center; gap: 3px;
  }
  .contact-divider__rule { flex: 1; height: 1px; background: var(--ink); }
  .contact-divider svg { width: 24px; height: 24px; }

  .contact {
    position: absolute; top: 480px; left: 0; right: 0;
    text-align: center; font-size: 16.5px; line-height: 22px; color: var(--ink);
  }

  .company {
    position: absolute; top: 240px; left: 0; right: 0;
    display: flex; flex-direction: column; align-items: center; gap: 20px;
  }
  .company__dot { width: 70px; height: 70px; border-radius: 50%; background: var(--bronze); }
  .company__name {
    font-family: "Bebas Neue", sans-serif;
    color: var(--ink); font-size: 33px; line-height: 1.05; text-align: center;
  }
</style>
</head>
<body>
  <section class="card card--front">
    <div class="brand-mark">
      <div class="brand-mark__dot"></div>
      <div class="brand-mark__name">Old Orchard<br>Salvage Co.</div>
    </div>

    <div class="person">
      <p class="person__name">Walter J. Brennick, ISA</p>
      <p class="person__role">Buyer, Broker, Consultant and Appraiser</p>
    </div>

    <div class="contact-divider">
      <span class="contact-divider__rule"></span>
      <svg viewBox="0 0 24 24" aria-label="Phone"><circle cx="12" cy="12" r="12" fill="var(--copper)"/><path d="M7 10c0-2 2-3 5-3s5 1 5 3l-2 1-1-2h-4l-1 2zM8 12h8l1 5H7z" fill="#fff"/></svg>
      <svg viewBox="0 0 24 24" aria-label="Email"><circle cx="12" cy="12" r="12" fill="var(--copper)"/><rect x="6.5" y="8" width="11" height="8" fill="#fff"/><path d="M6.5 8l5.5 4.5L17.5 8" fill="none" stroke="var(--copper)" stroke-width="1.2"/></svg>
      <svg viewBox="0 0 24 24" aria-label="Website"><circle cx="12" cy="12" r="12" fill="var(--copper)"/><circle cx="12" cy="12" r="6" fill="none" stroke="#fff" stroke-width="1.5"/><path d="M6 12h12M12 6c-3 3-3 9 0 12M12 6c3 3 3 9 0 12" fill="none" stroke="#fff" stroke-width="1.2"/></svg>
      <span class="contact-divider__rule"></span>
    </div>

    <div class="contact">
      <p>555-302-71938</p>
      <p>walter@oldorchardsalvage.example</p>
      <p>www.oldorchardsalvage.example</p>
    </div>
  </section>

  <section class="card card--back">
    <div class="company">
      <div class="company__dot"></div>
      <p class="company__name">Walter Brennick's<br>Old Orchard Salvage Co.</p>
    </div>
  </section>
</body>
</html>
```